Redesign business cards

We have a new logo and I am not that happy with the layout of our existing card and looking for a change. Font is a bit small and the green can be hard to read. Logo may need a tidy up as the copy I have is not that hi-res too so require you to produce a hi-res version of the logo for us too. There will be three individual business cards to produce with just the names and phone numbers being different. Address will change too, but use what you see on the card for now.

Industry/Entity Type

Business

Requirements
Nice to have
• You could consider a redesign to the new logo, just not too radical. We like the blue and green hexagons as we feel that they are representative of oil industry that we are in.

```html
<!DOCTYPE html>
<html lang="en">
<head>
<meta charset="utf-8">
<title>Tidewell Oil Services – Business Card</title>
<link href="https://fonts.googleapis.com/css2?family=Arimo:wght@400;700&display=swap" rel="stylesheet">
<style>
  :root {
    --backdrop: #4b5661;
    --card: #ffffff;
    --brand-blue: #29a8e0;
    --brand-green: #8cc63f;
    --ink: #111111;
    --icon-grey: #8a8a8a;
  }
  * { box-sizing: border-box; margin: 0; padding: 0; }
  html, body {
    width: 1200px; height: 1000px; overflow: hidden;
    background: var(--backdrop);
    font-family: "Arimo", Arial, sans-serif;
  }
  .business-card {
    position: absolute; left: 100px; top: 215px;
    width: 1000px; height: 570px;
    background: var(--card);
    box-shadow: 0 18px 40px rgba(0,0,0,0.35);
    overflow: hidden;
  }
  .holder {
    position: absolute; right: 60px; top: 52px; text-align: right;
  }
  .holder-name { color: var(--brand-blue); font-size: 36px; font-weight: 400; }
  .holder-role { color: var(--brand-green); font-size: 28px; margin-top: 6px; }
  .wordmark {
    position: absolute; left: 80px; top: 250px;
    display: flex; align-items: center; gap: 18px;
  }
  .wordmark-dot { width: 46px; height: 46px; border-radius: 50%; background: var(--brand-green); }
  .wordmark-name { color: var(--brand-blue); font-size: 64px; font-weight: 700; line-height: 1; }
  .contact-list {
    position: absolute; left: 560px; top: 215px; list-style: none;
  }
  .contact-item {
    display: flex; align-items: center; gap: 22px;
    font-size: 30px; color: var(--ink); margin-bottom: 10px;
  }
  .contact-icon { width: 24px; height: 24px; fill: var(--icon-grey); flex: none; }
  .address-band {
    position: absolute; left: 0; bottom: 0; width: 100%; height: 100px;
    background: var(--brand-blue);
    display: flex; align-items: center; gap: 16px; padding-left: 50px;
    color: #ffffff; font-size: 25px;
  }
  .pin-icon { width: 24px; height: 30px; fill: #ffffff; flex: none; }
</style>
</head>
<body>
  <div class="business-card">
    <div class="holder">
      <p class="holder-name">Daniel Harwood NZCE (Mech) P&amp;P</p>
      <p class="holder-role">Director</p>
    </div>

    <div class="wordmark">
      <span class="wordmark-dot"></span>
      <span class="wordmark-name">Tidewell</span>
    </div>

    <ul class="contact-list">
      <li class="contact-item">
        <svg class="contact-icon" viewBox="0 0 24 24" aria-hidden="true"><path d="M6.6 10.8a15 15 0 0 0 6.6 6.6l2.2-2.2a1 1 0 0 1 1-.25 11.4 11.4 0 0 0 3.6.57 1 1 0 0 1 1 1V20a1 1 0 0 1-1 1A17 17 0 0 1 3 4a1 1 0 0 1 1-1h3.5a1 1 0 0 1 1 1c0 1.25.2 2.45.57 3.57a1 1 0 0 1-.25 1z"/></svg>
        <span>+61 400 555 018</span>
      </li>
      <li class="contact-item">
        <svg class="contact-icon" viewBox="0 0 24 24" aria-hidden="true"><path d="M2 5h20v14H2z" fill="none"/><path d="M2 5h20v2l-10 6L2 7zM2 9l10 6 10-6v10H2z"/></svg>
        <span>daniel@greenmere.co.nz</span>
      </li>
      <li class="contact-item">
        <svg class="contact-icon" viewBox="0 0 24 24" aria-hidden="true"><path d="M12 2a10 10 0 1 0 0 20 10 10 0 0 0 0-20zm0 2c.9 1.2 1.6 2.6 2 4h-4c.4-1.4 1.1-2.8 2-4zM4.3 14a8 8 0 0 1 0-4h3.4a17 17 0 0 0 0 4zm.9 2h3c.3 1.2.8 2.4 1.4 3.4A8 8 0 0 1 5.2 16zm3-8h-3a8 8 0 0 1 4.4-3.4C8.9 5.6 8.5 6.8 8.2 8zM12 20c-.9-1.2-1.6-2.6-2-4h4c-.4 1.4-1.1 2.8-2 4zm2.3-6H9.7a15 15 0 0 1 0-4h4.6a15 15 0 0 1 0 4zm.1 5.4c.6-1 1.1-2.2 1.4-3.4h3a8 8 0 0 1-4.4 3.4zM16.3 14a17 17 0 0 0 0-4h3.4a8 8 0 0 1 0 4zm-.5-6c-.3-1.2-.8-2.4-1.4-3.4A8 8 0 0 1 18.8 8z"/></svg>
        <span>www.tidewell.com.au</span>
      </li>
    </ul>

    <div class="address-band">
      <svg class="pin-icon" viewBox="0 0 24 30" aria-hidden="true"><path d="M12 0a11 11 0 0 0-11 11c0 8 11 19 11 19s11-11 11-19A11 11 0 0 0 12 0zm0 15a4 4 0 1 1 0-8 4 4 0 0 1 0 8z"/></svg>
      <span>Tidewell Oil Services 215 Harbour Road / PO Box 4410 / Eastbrook Queensland 4000</span>
    </div>
  </div>
</body>
</html>
```